Corporate Business Card

Very professional, Modern, Not to busy, include phone address email, website
(253) 617-4930, 18761 52nd Avenue S, Kent, WA 98047, martin@plumlinegroup.com, varkoworks.com

Target Market(s)

Manufacturing

Industry/Entity Type

Aero, machining, manufacturing, Off road racing

Contact Information for Business Card

Phone, address email, website

```html
<!DOCTYPE html>
<html lang="en">
<head>
<meta charset="UTF-8">
<title>Varko Works – Business Card</title>
<link rel="stylesheet" href="https://fonts.googleapis.com/css2?family=Montserrat:wght@500;700&display=swap">
<style>
  :root {
    --navy: #17356f;
    --red: #d9222a;
    --white: #ffffff;
    --silver: #c9cdd3;
    --ink: #1a1a1a;
    --backdrop: #e9e6e1;
  }
  html, body {
    margin: 0;
    padding: 0;
    width: 1200px;
    height: 1023px;
    overflow: hidden;
    background: var(--backdrop);
    font-family: "Montserrat", sans-serif;
  }
  .card {
    position: absolute;
    width: 560px;
    height: 320px;
    border-radius: 22px;
    overflow: hidden;
    box-shadow: 0 10px 28px rgba(0,0,0,0.18);
  }
  .card-front {
    left: 110px;
    top: 110px;
    background: var(--navy);
  }
  .card-back {
    left: 530px;
    top: 590px;
    background: var(--white);
  }
  .brand-name {
    position: absolute;
    font-weight: 700;
    letter-spacing: 2px;
    white-space: nowrap;
    text-transform: uppercase;
  }
  .card-front .brand-name {
    left: 0;
    right: 0;
    top: 128px;
    text-align: center;
    font-size: 46px;
    color: var(--silver);
  }
  .card-back .brand-name {
    right: 40px;
    top: 48px;
    font-size: 30px;
    color: var(--navy);
  }
  .wave {
    position: absolute;
    left: 0;
    top: 0;
    width: 560px;
    height: 320px;
  }
  .address {
    position: absolute;
    left: 40px;
    top: 112px;
    font-size: 14px;
    font-weight: 500;
    line-height: 1.45;
    color: var(--ink);
  }
  .contact-list {
    position: absolute;
    left: 40px;
    top: 196px;
    margin: 0;
    padding: 0;
    list-style: none;
    font-size: 13px;
    font-weight: 500;
    color: var(--ink);
  }
  .contact-list li {
    display: flex;
    align-items: center;
    gap: 8px;
    height: 22px;
  }
  .contact-list svg {
    width: 13px;
    height: 13px;
    fill: var(--red);
    flex: none;
  }
</style>
</head>
<body>

<section class="card card-front" aria-label="Card front">
  <div class="brand-name">Varko Works</div>
</section>

<section class="card card-back" aria-label="Card back">
  <svg class="wave" viewBox="0 0 560 320" aria-hidden="true">
    <path d="M0,320 L0,312 C160,306 250,280 330,215 C410,150 480,128 560,122 L560,320 Z" fill="var(--navy)"/>
    <path d="M120,300 C230,290 280,250 340,195 C400,140 460,112 545,102 C470,118 410,150 348,205 C290,258 230,294 120,300 Z" fill="var(--red)"/>
  </svg>

  <div class="brand-name">Varko Works</div>

  <div class="address">18761 52nd Avenue<br>S, Kent, WA 98047</div>

  <ul class="contact-list">
    <li>
      <svg viewBox="0 0 16 16"><path d="M3.5 1.5 6 4 4.6 6c.8 2 2.4 3.6 4.4 4.4L11 9l2.5 2.5-1.6 2.3C6.5 13.5 2.5 9.5 1.2 3.1z"/></svg>
      (253) 617-4930
    </li>
    <li>
      <svg viewBox="0 0 16 16"><path d="M1 3h14v10H1z M1.5 3.5 8 9l6.5-5.5" stroke="#fff" stroke-width="1.2"/></svg>
      martin@plumlinegroup.com
    </li>
    <li>
      <svg viewBox="0 0 16 16"><circle cx="8" cy="8" r="7"/><path d="M1 8h14M8 1c-3 3-3 11 0 14M8 1c3 3 3 11 0 14" stroke="#fff" stroke-width="1" fill="none"/></svg>
      www.varkoworks.com
    </li>
  </ul>
</section>

</body>
</html>
```